Business Cards Design for the electrical wholesaler: clean bold dynamic :)

We need a business card design that would follow our latest brand guidelines. As an electrical wholesaler we want to bring a fresh look and feel into the industry. The design should be clean bold and dynamic. It should come alive with the renewed energy of our green colour. Our grey colour should keep things balanced and complement the notion of maturity and responsibility. We employ Lato as a corporate font however are not bound by this font and we’re open to interpretation here.

Target Market(s)

Electrical contractors

Industry/Entity Type

Business

Contact Information for Business Card

Logo
Name & Surname: Halyna Dorosh
Job Title: Director of Marketing
Email: halya.dorosh@quillmail.example
Cell phone: XXX.XXX.XXXX
Address: 20517 - 87 Ave. Edmonton, AB, Canada. T6K 4N8
Business Phone: 780.555.0184
Website: www.brovix.example

Font styles to use
Other font styles liked:
• Lato

Requirements
Must have
• Logo & website
Nice to have
• Brand elements - some of them you may find in the attached Brand Guidelines (e.g. three lines on the background signifying "W")

```html
<!DOCTYPE html>
<html lang="en">
<head>
<meta charset="utf-8">
<title>Brovix Business Cards</title>
<link rel="stylesheet" href="https://fonts.googleapis.com/css2?family=Lato:wght@400;700&display=swap">
<style>
  :root {
    --brand-green: #6cc000;
    --brand-green-dark: #62b000;
    --brand-grey: #4a4a4c;
    --band-black: #1b1b1b;
    --card-white: #f7f8f8;
    --ink: #2a2a2a;
    --backdrop: #e9e6e1;
  }
  * { box-sizing: border-box; margin: 0; padding: 0; }
  html, body {
    width: 1200px; height: 800px; overflow: hidden;
    background: var(--backdrop);
    font-family: "Lato", sans-serif;
  }
  .sheet {
    position: relative; width: 1200px; height: 800px;
    display: flex; align-items: center; justify-content: center; gap: 40px;
  }
  .card {
    position: relative; width: 540px; height: 309px; overflow: hidden;
    box-shadow: 0 10px 26px rgba(0,0,0,.18);
  }

  /* Front */
  .card--front { background: var(--brand-green); }
  .front-brand {
    position: absolute; left: 60px; top: 92px;
    display: flex; align-items: center; gap: 12px;
  }
  .brand-square { width: 30px; height: 30px; background: var(--brand-grey); }
  .brand-name {
    font-weight: 700; font-size: 50px; color: var(--brand-grey); letter-spacing: -1px;
  }
  .front-web-band {
    position: absolute; right: 0; top: 150px; width: 250px; height: 28px;
    background: linear-gradient(90deg, rgba(27,27,27,0), #2b2b2b 35%, #4a4a4a);
    display: flex; align-items: center; justify-content: flex-end; padding-right: 14px;
    font-size: 12px; color: #fff; letter-spacing: .5px;
  }
  .front-web-band b { font-weight: 700; }
  .front-black-band {
    position: absolute; left: 0; right: 0; top: 214px; height: 44px;
    background: var(--band-black);
  }

  /* Back */
  .card--back { background: var(--card-white); }
  .back-brand {
    position: absolute; left: 44px; top: 82px;
    display: flex; align-items: center; gap: 10px;
  }
  .back-brand .brand-name { font-size: 44px; }
  .back-brand .brand-square { width: 26px; height: 26px; background: var(--brand-green); }
  .divider {
    position: absolute; left: 262px; top: 40px; width: 1px; height: 140px;
    background: linear-gradient(180deg, rgba(0,0,0,0), rgba(0,0,0,.28), rgba(0,0,0,0));
  }
  .contact { position: absolute; left: 292px; top: 44px; width: 236px; color: var(--ink); }
  .contact-name { font-size: 19px; font-weight: 400; }
  .contact-title { font-size: 13px; color: var(--brand-green); margin-top: 2px; }
  .contact-list { list-style: none; margin-top: 18px; font-size: 11px; line-height: 1.4; }
  .contact-list li { display: flex; gap: 7px; margin-bottom: 6px; }
  .contact-list svg { flex: none; margin-top: 2px; }
  .back-black-band {
    position: absolute; left: 0; right: 0; top: 214px; height: 48px;
    background: linear-gradient(90deg, var(--band-black) 70%, #3a3a3a);
    display: flex; align-items: center; justify-content: flex-end; padding-right: 52px;
    font-size: 13px; color: var(--brand-green); letter-spacing: .6px;
  }
  .back-black-band b { font-weight: 700; }
</style>
</head>
<body>
<main class="sheet">
  <section class="card card--front" aria-label="Card front">
    <div class="front-brand">
      <span class="brand-square"></span>
      <span class="brand-name">brovix</span>
    </div>
    <div class="front-web-band">www.<b>brovix</b>.example</div>
    <div class="front-black-band"></div>
  </section>

  <section class="card card--back" aria-label="Card back">
    <div class="back-brand">
      <span class="brand-square"></span>
      <span class="brand-name">brovix</span>
    </div>
    <div class="divider"></div>
    <div class="contact">
      <h1 class="contact-name">Halyna Dorosh</h1>
      <p class="contact-title">Director of Marketing</p>
      <ul class="contact-list">
        <li>
          <svg width="9" height="12" viewBox="0 0 9 12" aria-hidden="true"><path d="M4.5 0A4.5 4.5 0 0 0 0 4.5C0 8 4.5 12 4.5 12S9 8 9 4.5A4.5 4.5 0 0 0 4.5 0zm0 6.3a1.8 1.8 0 1 1 0-3.6 1.8 1.8 0 0 1 0 3.6z" fill="var(--brand-green)"/></svg>
          <span>20517 - 87 Ave. Edmonton,<br>AB, Canada. T6K 4N8</span>
        </li>
        <li>
          <svg width="9" height="12" viewBox="0 0 9 12" aria-hidden="true"><rect x=".7" y=".7" width="7.6" height="10.6" rx="1.2" fill="none" stroke="var(--brand-green)" stroke-width="1.4"/><circle cx="4.5" cy="9.3" r=".8" fill="var(--brand-green)"/></svg>
          <span>780.555.0184</span>
        </li>
        <li>
          <svg width="11" height="10" viewBox="0 0 11 10" aria-hidden="true"><rect x=".6" y="1.6" width="9.8" height="7.4" rx="1" fill="none" stroke="var(--brand-green)" stroke-width="1.2"/><path d="M.8 2l4.7 3.6L10.2 2" fill="none" stroke="var(--brand-green)" stroke-width="1.2"/></svg>
          <span>halya.dorosh@quillmail.example</span>
        </li>
      </ul>
    </div>
    <div class="back-black-band">www.<b>brovix</b>.example</div>
  </section>
</main>
</body>
</html>
```